Computer Training in the Education sector - Letterhead

We need a new letter head to be designed for the company. We provide computer training fro the Education Sector, both primary and private tertiary providers. The colours will need to tie in with the website www.crossingthestream.co.nz.
The company name is Crossing the Stream with the tag line of Computer Training for Educators.
The footer will need to have the following detail...
0508 PCS MENTOR
021 839 415
www.crossingthestream.co.nz / training@crossingthestream.co.nz
Updates

Thanks for the designs so far.

Some have watermarks in the background. Please don't worry about using watermarks as I will not be using a watermark in in a final design.
Regards,
Roger

Thank you for all the designs and the effort. There was some great concepts that came through.

Cheers
Roger

Industry/Entity Type

Computer

```html
<!DOCTYPE html>
<html lang="en">
<head>
<meta charset="utf-8">
<title>Crossing the Stream – Letterhead</title>
<link rel="stylesheet" href="https://fonts.googleapis.com/css2?family=Questrial&family=Jost:wght@700&display=swap">
<style>
  :root {
    --backdrop: #e9e6e1;
    --paper: #ffffff;
    --ink: #3a3a3a;
    --rule: #6d6d6d;
    --brand-blue: #2f73b7;
    --brand-orange: #e4823a;
    --brand-green: #8bb73f;
  }
  html, body {
    margin: 0;
    padding: 0;
    width: 1034px;
    height: 1200px;
    overflow: hidden;
    background: var(--backdrop);
  }
  .letterhead {
    position: absolute;
    left: 53px;
    top: 0;
    width: 928px;
    height: 1200px;
    background: var(--paper);
    overflow: hidden;
    box-shadow: 0 0 6px rgba(0,0,0,0.18);
  }
  .brand {
    position: absolute;
    left: 31px;
    top: 40px;
    width: 150px;
    display: flex;
    flex-direction: column;
    align-items: flex-start;
    gap: 10px;
  }
  .brand-dot {
    width: 22px;
    height: 22px;
    border-radius: 50%;
    background: var(--brand-orange);
  }
  .brand-name {
    font-family: "Questrial", sans-serif;
    font-size: 29px;
    line-height: 1.05;
    color: var(--brand-blue);
  }
  .contact {
    position: absolute;
    left: 617px;
    top: 59px;
    height: 84px;
    padding-left: 22px;
    border-left: 1px solid var(--rule);
    font-family: "Questrial", sans-serif;
    font-style: normal;
    font-size: 16px;
    color: var(--ink);
  }
  .contact-line {
    display: flex;
    align-items: center;
    height: 22.5px;
    gap: 7px;
  }
  .contact-line svg {
    width: 13px;
    height: 13px;
    flex: none;
  }
  .footer-band {
    position: absolute;
    left: 0;
    bottom: 0;
    width: 928px;
    height: 140px;
    background: linear-gradient(180deg,
      rgba(139,183,63,0) 0%,
      rgba(139,183,63,0.55) 18%,
      rgba(228,130,58,0.85) 40%,
      var(--brand-blue) 62%,
      var(--brand-blue) 100%);
  }
  .tagline {
    position: absolute;
    right: 40px;
    bottom: 33px;
    margin: 0;
    font-family: "Jost", sans-serif;
    font-weight: 700;
    font-size: 21px;
    letter-spacing: 1.6px;
    color: #ffffff;
  }
</style>
</head>
<body>
  <main class="letterhead">
    <header>
      <div class="brand">
        <span class="brand-dot"></span>
        <span class="brand-name">Crossing the Stream</span>
      </div>
      <address class="contact">
        <div class="contact-line">
          <svg viewBox="0 0 16 16" aria-hidden="true"><circle cx="8" cy="8" r="7" fill="none" stroke="#3a3a3a" stroke-width="1.4"/><path d="M5 4.5c0 4 2.5 7 6 7l.8-1.6-1.8-1-1 .9C7.6 9.3 6.6 8.3 6.2 7l.9-1-1-1.8z" fill="#3a3a3a"/></svg>
          <span>0508 PCS MENTOR</span>
        </div>
        <div class="contact-line">
          <svg viewBox="0 0 16 16" aria-hidden="true"><circle cx="8" cy="8" r="7" fill="none" stroke="#3a3a3a" stroke-width="1.4"/><path d="M5 4.5c0 4 2.5 7 6 7l.8-1.6-1.8-1-1 .9C7.6 9.3 6.6 8.3 6.2 7l.9-1-1-1.8z" fill="#3a3a3a"/></svg>
          <span>021 839 415</span>
        </div>
        <div class="contact-line">
          <svg viewBox="0 0 16 16" aria-hidden="true"><path d="M1.5 6.5 8 2l6.5 4.5V13h-13z" fill="#3a3a3a"/><path d="M2.5 6.8 8 10.5l5.5-3.7" fill="none" stroke="#fff" stroke-width="1.2"/></svg>
          <span>training@crossingthestream.co.nz</span>
        </div>
        <div class="contact-line">
          <svg viewBox="0 0 16 16" aria-hidden="true"><g fill="none" stroke="#3a3a3a" stroke-width="1.2"><circle cx="8" cy="8" r="6.5"/><ellipse cx="8" cy="8" rx="3" ry="6.5"/><path d="M1.5 8h13M2.5 4.8h11M2.5 11.2h11"/></g></svg>
          <span>www.crossingthestream.co.nz</span>
        </div>
      </address>
    </header>

    <footer>
      <div class="footer-band" role="img" aria-label="Decorative footer band in brand green, orange and blue"></div>
      <p class="tagline">Computer Training for Educators</p>
    </footer>
  </main>
</body>
</html>
```